Brambleton Pizza Website

We are working with Brambleton Pizza and designing them a website.

Some sites to use for content/competitors and inspiration:

https://fennimores.com
https://www.bhq-eats.com
https://brightorchard.com/en-us/

Thank you for taking the time to consider designing a website for us. We are web developers based in Stockton, CA, USA. Most of our projects go through the same process. Understanding this process may help you win a project with us. We custom-code all of our websites in-house. We don’t have any requirements as to what tools you use for your design, but we prefer Figma files. For any design that we label as four-stars, we send it to the client for review. The client picks the final design they want us to use. Once we complete this process, we will continue to show additional clients all the four-star sites and purchase them later. Your designs will have multiple chances to sell. For better chances of success, we ask that you follow these guidelines.

IMAGES:
If you use any images or icons in the design, we ask that you have a link to the asset so we can purchase the image/icon. Most of the designs we submit do not have the customer’s images on them unless they have some great images. Be creative; show us the feeling you are trying to portray with your image choices. Use any royalty-free site you choose. We subscribe to Quillstone and mainly use their images, but we can purchase images outside of Quillstone.

PLEASE NOTE: we will not submit designs to clients with watermarks on the images.

FONTS:
We ask that you identify the fonts used in the design. This can be done in a message if you want. We typically use Google Fonts and Quillstone Fonts.

CONTENT:
We're always open to different content and ideas. We often submit designs with stock images so the client can see our vision. We typically take pictures after the website launch to use their images with our vision. Lorem Ipsum is fine for paragraphs, but we ask that you write the headers in correct English. We want to be able to show the vision and identify the sections of the website.

INSPIRATION:
We typically add a couple of links in the brief of websites we like to help you get started in your design.

REVISIONS:
We do not often ask for revisions of the designs unless we see something in the design that may not appeal to the client. If there are slight changes that we want to make, we do that in the development process.

FEEDBACK:
We rarely give feedback on designs during the design process. We are working on many website projects and do not have the time to provide feedback. We usually respond if your request is well thought out and asks specific questions, but a note asking “feedback, please” usually goes unanswered.

```html
<!DOCTYPE html>
<html lang="en">
<head>
<meta charset="utf-8">
<title>Brambleton Pizza</title>
<link href="https://fonts.googleapis.com/css2?family=Outfit:wght@300;400;500;600;700&family=Poppins:wght@300;400;500;600;700&display=swap" rel="stylesheet">
<style>
:root{
  --green:#2ba637;
  --green-soft:#f1faf0;
  --red:#d62a2a;
  --ink:#111111;
  --black:#050505;
  --grey-band:#efefef;
  --card:#e9e9e9;
  --white:#ffffff;
  --gold:#f2c21b;
}
*{margin:0;padding:0;box-sizing:border-box}
html,body{width:1200px;height:4494px;overflow:hidden}
body{position:relative;background:var(--white);font-family:"Poppins",sans-serif;color:var(--ink)}
.abs{position:absolute}
.heading{font-family:"Outfit",sans-serif;font-weight:400}
.btn{position:absolute;display:flex;align-items:center;justify-content:center;border-radius:30px;background:var(--green);color:var(--white);font-family:"Poppins",sans-serif}
.eyebrow{position:absolute;color:var(--green);font-size:14px;display:flex;align-items:center;gap:6px;text-transform:uppercase}
.eyebrow::before,.eyebrow::after{content:"";width:30px;height:1px;background:var(--red)}
.eyebrow.left::before{display:none}

/* header + hero */
.hero{position:absolute;left:0;top:0;width:1200px;height:658px;background:var(--black)}
.hero-photo{position:absolute;left:0;top:154px;width:602px;height:504px;background:radial-gradient(circle at 45% 40%,#d99a3a 0,#b5611f 30%,#5a2b10 50%,#151008 75%,#070707 100%)}
.brand{position:absolute;left:70px;top:44px;width:175px;text-align:center;color:var(--white);font-family:"Outfit",sans-serif;font-weight:600;font-size:22px;line-height:1.1;letter-spacing:1px;text-transform:uppercase}
.nav{position:absolute;top:98px;left:0;width:1200px;height:24px;font-size:13px;color:var(--white)}
.nav a{position:absolute;transform:translateX(-50%);color:var(--white);text-decoration:none;white-space:nowrap}
.nav a.active{border-bottom:2px solid var(--red);padding-bottom:3px}
.search{position:absolute;left:849px;top:37px;width:173px;height:31px;border:1.5px solid var(--white);border-radius:16px;color:var(--red);font-size:11px;padding:7px 14px}
.hero-title{position:absolute;left:541px;top:240px;color:var(--white);font-size:72px;line-height:86px;font-family:"Outfit",sans-serif;font-weight:400}
.hero-text{position:absolute;left:541px;top:432px;width:600px;color:var(--white);font-size:12.5px;line-height:16px}
.btn-outline{position:absolute;display:flex;align-items:center;justify-content:center;border:2px solid var(--red);border-radius:30px;color:var(--white);font-size:18px}

/* about */
.about{position:absolute;left:0;top:658px;width:1200px;height:455px;background:var(--grey-band)}
.about-photo{position:absolute;left:160px;top:24px;width:372px;height:399px;border-radius:186px 186px 0 0;background:radial-gradient(circle at 50% 50%,#d88b34 0,#a8441c 40%,#3a2a20 75%,#5b6470 100%)}
.about-title{position:absolute;left:616px;top:106px;font-size:48px}
.about-text{position:absolute;left:616px;top:170px;width:430px;font-size:13px;line-height:22.5px;color:#222}

/* menus */
.section-title{position:absolute;left:0;width:1200px;text-align:center;font-size:48px}
.menu-card{position:absolute;width:321px;height:323px;background:var(--card);border-radius:54px;box-shadow:0 6px 6px rgba(0,0,0,.22);text-align:center}
.menu-photo{position:absolute;left:73px;top:-75px;width:175px;height:175px;border-radius:50%;background:radial-gradient(circle,#e0a047 0,#c4692c 55%,#7a3b18 72%,#2a1a10 80%,#e9e9e9 81%);box-shadow:0 4px 6px rgba(0,0,0,.25)}
.menu-name{position:absolute;left:0;top:125px;width:100%;color:var(--red);font-size:21px;font-family:"Outfit",sans-serif}
.menu-desc{position:absolute;left:30px;top:164px;width:261px;font-size:13px;line-height:17px}
.menu-price{position:absolute;left:0;top:205px;width:100%;font-size:17px;font-weight:500}
.menu-card .btn{left:98px;top:241px;width:124px;height:38px;font-size:13px}

/* stats */
.stats{position:absolute;left:0;top:2342px;width:1200px;height:391px;background:var(--green-soft)}
.stat-divider{position:absolute;top:42px;width:2px;height:303px;background:var(--red)}
.stat{position:absolute;top:100px;width:240px;text-align:center}
.stat svg{display:block;margin:0 auto;height:96px}
.stat-num{margin-top:20px;color:var(--red);font-family:"Outfit",sans-serif;font-weight:600;font-size:38px;line-height:40px}
.stat-label{margin-top:8px;font-size:20px}

/* offer */
.offer{position:absolute;left:0;top:2733px;width:1200px;height:460px;background:linear-gradient(90deg,#141414 0,#1c1a18 55%,#2a2016 100%)}
.offer-photo{position:absolute;left:724px;top:31px;width:450px;height:401px;border-radius:50%;background:radial-gradient(circle at 60% 40%,#e2a23e 0,#c05e22 45%,#6a3214 68%,rgba(30,20,15,0) 72%)}
.offer-sub{position:absolute;left:66px;top:44px;color:var(--white);font-family:"Outfit",sans-serif;font-size:56px;line-height:60px}
.offer-big{position:absolute;left:66px;top:106px;color:var(--white);font-family:"Poppins",sans-serif;font-weight:600;font-size:90px;line-height:96px}
.offer-text{position:absolute;left:66px;top:311px;width:560px;color:var(--white);font-size:12.5px;line-height:16px}

/* testimonials */
.t-frame{position:absolute;left:328px;top:3396px;width:588px;height:441px;border:3px solid #222;border-radius:6px}
.t-green{position:absolute;left:228px;top:3474px;width:784px;height:304px;background:var(--green)}
.quote-badge{position:absolute;width:52px;height:52px;border-radius:50%;background:var(--white);box-shadow:0 2px 8px rgba(0,0,0,.2);display:flex;align-items:center;justify-content:center;font-family:Georgia,serif;font-weight:700;font-size:34px;line-height:1;padding-top:14px}
.avatar{position:absolute;left:562px;top:3419px;width:115px;height:115px;border-radius:50%;background:radial-gradient(circle,#c9c9c9,#8a8a8a);border:3px solid var(--white)}
.t-text{position:absolute;left:350px;top:3580px;width:540px;text-align:center;color:var(--white);font-size:14px;line-height:24px}
.t-name{position:absolute;left:0;top:3670px;width:1200px;text-align:center;color:#fff7c4;font-size:19px}
.t-stars{position:absolute;left:0;top:3698px;width:1200px;text-align:center;color:var(--gold);font-size:17px;letter-spacing:4px}
.arrow{position:absolute;width:36px;height:36px;border-radius:50%;display:flex;align-items:center;justify-content:center}

/* newsletter */
.newsletter{position:absolute;left:0;top:3903px;width:1200px;height:279px;background:linear-gradient(90deg,#2a2018,#1a1512 50%,#2a1d14)}
.nl-title{position:absolute;left:0;top:32px;width:1200px;text-align:center;color:var(--white);font-weight:600;font-size:44px}
.nl-sub{position:absolute;left:0;top:113px;width:1200px;text-align:center;color:var(--white);font-size:20px}
.nl-input{position:absolute;left:164px;top:187px;width:696px;height:52px;background:var(--white);color:#888;font-size:16px;padding:14px 22px}
.nl-submit{position:absolute;left:872px;top:187px;width:173px;height:52px;background:var(--green);color:var(--white);font-size:16px;display:flex;align-items:center;justify-content:center}

/* footer */
.footer{position:absolute;left:0;top:4182px;width:1200px;height:250px;background:var(--black);color:var(--white)}
.contact-item{position:absolute;top:76px;display:flex;gap:14px;font-size:16px;line-height:25px}
.contact-icon{width:34px;height:34px;border-radius:50%;background:var(--white);flex:none;display:flex;align-items:center;justify-content:center}
.footer-rule{position:absolute;left:63px;top:183px;width:1069px;height:1px;background:#555}
.footer-nav{position:absolute;top:206px;left:0;width:1200px;font-size:13px}
.footer-nav a{position:absolute;transform:translateX(-50%);color:var(--white);text-decoration:none;white-space:nowrap}
.footer-nav i{position:absolute;top:2px;width:1px;height:18px;background:#aaa}
.bottom-bar{position:absolute;left:0;top:4432px;width:1200px;height:62px;background:#f4f4f4}
.copyright{position:absolute;left:66px;top:20px;font-size:15px}
.social{position:absolute;top:13px;width:36px;height:36px;border-radius:50%;background:var(--green)}
</style>
</head>
<body>

<header class="hero">
  <div class="hero-photo" role="img" aria-label="Pepperoni and vegetable pizza on a wooden board with onion rings and broccoli"></div>
  <div class="brand">Brambleton<br>Pizza</div>
  <div class="search">Search
    <svg class="abs" style="right:12px;top:6px" width="18" height="18" viewBox="0 0 18 18"><circle cx="7.5" cy="7.5" r="5.5" fill="none" stroke="#fff" stroke-width="1.6"/><line x1="11.5" y1="11.5" x2="16" y2="16" stroke="#fff" stroke-width="1.6"/></svg>
  </div>
  <svg class="abs" style="left:1042px;top:36px" width="28" height="28" viewBox="0 0 28 28"><path d="M2 5h4l3 13h13l3-9H8" fill="none" stroke="#fff" stroke-width="2"/><circle cx="11" cy="23" r="2" fill="#fff"/><circle cx="20" cy="23" r="2" fill="#fff"/><circle cx="24" cy="4" r="3.5" fill="#2ba637"/></svg>
  <svg class="abs" style="left:1092px;top:38px" width="28" height="28" viewBox="0 0 28 28"><circle cx="14" cy="9" r="6" fill="none" stroke="#fff" stroke-width="2"/><path d="M3 26c1-7 6-9 11-9s10 2 11 9z" fill="none" stroke="#fff" stroke-width="2"/></svg>
  <nav class="nav">
    <a class="active" style="left:466px">Home</a>
    <a style="left:555px">Our Menus</a>
    <a style="left:668px">About Us</a>
    <a style="left:778px">Order Online</a>
    <a style="left:878px">Gallery</a>
    <a style="left:977px">Reviews</a>
    <a style="left:1085px">Contact Us</a>
  </nav>
  <h1 class="hero-title">A Slice Of Heaven<br>In Every Bite pizza</h1>
  <p class="hero-text">Lorem ipsum dolor sit amet, consectetur adipiscing elit, sed do eiusmod tempor incididunt ut labore et dolore magna aliqua.</p>
  <a class="btn" style="left:544px;top:497px;width:222px;height:46px;font-size:18px">Book A Table</a>
  <a class="btn-outline" style="left:786px;top:497px;width:221px;height:46px">View Menu</a>
</header>

<section class="about">
  <div class="about-photo" role="img" aria-label="Slice of tomato and olive pizza being lifted with melted cheese"></div>
  <div class="eyebrow left" style="left:616px;top:86px">Who We Are</div>
  <h2 class="about-title heading">About Us</h2>
  <p class="about-text">Sed ut perspiciatis unde omnis iste natus error sit voluptatem accusantium doloremque laudantium, totam rem aperiam, eaque ipsa quae ab illo inventore veritatis et quasi architecto beatae vitae dicta sunt explicabo. Nemo enim ipsam voluptatem quia voluptas sit aspernatur aut odit aut fugit, sed quia consequuntur magni dolores eos qui ratione voluptatem sequi nesciunt.</p>
  <a class="btn" style="left:616px;top:346px;width:124px;height:34px;font-size:13px">Read More</a>
</section>

<section class="menus">
  <div class="eyebrow" style="left:0;width:1200px;justify-content:center;top:1210px">Order Online Now</div>
  <h2 class="section-title heading" style="top:1226px">Our Menus</h2>

  <article class="menu-card" style="left:87px;top:1404px">
    <div class="menu-photo" role="img" aria-label="Italian pizza"></div>
    <h3 class="menu-name">Italian Pizza</h3>
    <p class="menu-desc">Lorem ipsum dolor sit amet, consectetur adipiscing elit, sed do</p>
    <p class="menu-price">$25.00</p>
    <a class="btn">Read More</a>
  </article>
  <article class="menu-card" style="left:440px;top:1404px">
    <div class="menu-photo" role="img" aria-label="Roman pizza"></div>
    <h3 class="menu-name">Roman Pizza</h3>
    <p class="menu-desc">Lorem ipsum dolor sit amet, consectetur adipiscing elit, sed do</p>
    <p class="menu-price">$25.00</p>
    <a class="btn">Read More</a>
  </article>
  <article class="menu-card" style="left:792px;top:1404px">
    <div class="menu-photo" role="img" aria-label="Vegetable pizza"></div>
    <h3 class="menu-name">veg Pizza</h3>
    <p class="menu-desc">Lorem ipsum dolor sit amet, consectetur adipiscing elit, sed do</p>
    <p class="menu-price">$25.00</p>
    <a class="btn">Read More</a>
  </article>
  <article class="menu-card" style="left:87px;top:1880px">
    <div class="menu-photo" role="img" aria-label="Cheese pizza"></div>
    <h3 class="menu-name">Cheese Pizza</h3>
    <p class="menu-desc">Lorem ipsum dolor sit amet, consectetur adipiscing elit, sed do</p>
    <p class="menu-price">$25.00</p>
    <a class="btn">Read More</a>
  </article>
  <article class="menu-card" style="left:440px;top:1880px">
    <div class="menu-photo" role="img" aria-label="BBQ chicken pizza"></div>
    <h3 class="menu-name">BBQ Chicken Pizza</h3>
    <p class="menu-desc">Lorem ipsum dolor sit amet, consectetur adipiscing elit, sed do</p>
    <p class="menu-price">$25.00</p>
    <a class="btn">Read More</a>
  </article>
  <article class="menu-card" style="left:792px;top:1880px">
    <div class="menu-photo" role="img" aria-label="Stuffed crust pizza"></div>
    <h3 class="menu-name">Stuffed crust</h3>
    <p class="menu-desc">Lorem ipsum dolor sit amet, consectetur adipiscing elit, sed do</p>
    <p class="menu-price">$25.00</p>
    <a class="btn">Read More</a>
  </article>
  <a class="btn" style="left:516px;top:2251px;width:159px;height:41px;font-size:16px">View More</a>
</section>

<section class="stats">
  <span class="stat-divider" style="left:343px"></span>
  <span class="stat-divider" style="left:606px"></span>
  <span class="stat-divider" style="left:862px"></span>
  <div class="stat" style="left:114px">
    <svg viewBox="0 0 80 96" width="80"><path d="M22 40c-10 0-16 7-16 15 0 11 16 27 16 27s16-16 16-27c0-8-6-15-16-15z" fill="var(--green)"/><circle cx="22" cy="55" r="6" fill="#fff"/><path d="M60 8c-7 0-11 5-11 10 0 8 11 19 11 19s11-11 11-19c0-5-4-10-11-10z" fill="var(--green)"/><circle cx="60" cy="18" r="4" fill="#fff"/><path d="M30 84q20 0 28-20t2-26" fill="none" stroke="var(--green)" stroke-width="3" stroke-dasharray="3 5"/></svg>
    <p class="stat-num">50</p><p class="stat-label">Pizza Branches</p>
  </div>
  <div class="stat" style="left:361px">
    <svg viewBox="0 0 100 96" width="100"><path d="M50 22l8 16 18 3-13 12 3 18-16-8-16 8 3-18-13-12 18-3z" fill="var(--green)"/><path d="M22 20q-16 30 6 56 10 10 22 12M78 20q16 30-6 56-10 10-22 12" fill="none" stroke="var(--green)" stroke-width="5"/></svg>
    <p class="stat-num">30</p><p class="stat-label">Number of Awards</p>
  </div>
  <div class="stat" style="left:609px">
    <svg viewBox="0 0 90 96" width="90"><path d="M45 4l4 8 8 1-6 6 2 8-8-4-8 4 2-8-6-6 8-1z" fill="var(--green)"/><path d="M22 14l3 6 6 1-5 4 1 6-5-3-5 3 1-6-5-4 6-1zM68 14l3 6 6 1-5 4 1 6-5-3-5 3 1-6-5-4 6-1z" fill="var(--green)"/><circle cx="45" cy="46" r="12" fill="var(--green)"/><path d="M22 88c0-16 10-24 23-24s23 8 23 24z" fill="var(--green)"/><circle cx="68" cy="78" r="12" fill="var(--green)" stroke="#fff" stroke-width="3"/><path d="M62 78l5 5 8-9" fill="none" stroke="#fff" stroke-width="3"/></svg>
    <p class="stat-num">100</p><p class="stat-label">Happy Customer</p>
  </div>
  <div class="stat" style="left:858px">
    <svg viewBox="0 0 100 96" width="100"><circle cx="50" cy="30" r="12" fill="var(--green)"/><circle cx="28" cy="36" r="10" fill="var(--green)"/><circle cx="72" cy="36" r="10" fill="var(--green)"/><path d="M12 76c0-14 7-22 16-22s16 8 16 22zM56 76c0-14 7-22 16-22s16 8 16 22z" fill="var(--green)"/><path d="M30 80c0-20 9-32 20-32s20 12 20 32z" fill="var(--green)" stroke="#f1faf0" stroke-width="3"/></svg>
    <p class="stat-num">30</p><p class="stat-label">Staff</p>
  </div>
</section>

<section class="offer">
  <div class="offer-photo" role="img" aria-label="Two large pizzas with onion rings and fries on a dark table"></div>
  <p class="offer-sub">Amazing Offers Online</p>
  <h2 class="offer-big">50% OFF PIZZAS<br>ONLINE</h2>
  <p class="offer-text">Lorem ipsum dolor sit amet, consectetur adipiscing elit, sed do eiusmod tempor incididunt ut labore et dolore magna aliqua.</p>
  <a class="btn" style="left:66px;top:366px;width:143px;height:40px;font-size:16px">Order Now</a>
</section>

<section class="testimonials">
  <div class="eyebrow" style="left:0;width:1200px;justify-content:center;top:3261px">Our Reviews</div>
  <h2 class="section-title heading" style="top:3277px">Testimonials</h2>
  <div class="t-frame"></div>
  <div class="t-green"></div>
  <div class="quote-badge" style="left:400px;top:3375px">&ldquo;</div>
  <div class="quote-badge" style="left:774px;top:3806px">&rdquo;</div>
  <div class="avatar" role="img" aria-label="Customer portrait"></div>
  <p class="t-text">There are many variations of passages of Lorem Ipsum available, but the majority have suffered alteration in some form, by injected humour, or randomised words which don't look even slightly</p>
  <p class="t-name">MARCO ELLERY</p>
  <p class="t-stars">★★★★★</p>
  <span class="arrow" style="left:143px;top:3588px"><svg width="14" height="14" viewBox="0 0 14 14"><path d="M9 2L4 7l5 5" fill="none" stroke="#8fd18f" stroke-width="2"/></svg></span>
  <span class="arrow" style="left:1057px;top:3588px;background:#d9f2d6"><svg width="14" height="14" viewBox="0 0 14 14"><path d="M5 2l5 5-5 5" fill="none" stroke="#2ba637" stroke-width="2"/></svg></span>
</section>

<section class="newsletter">
  <h2 class="nl-title">SUBSCRIBE TO OUR NEWSLETTER</h2>
  <p class="nl-sub">Be the first to know about new products and exclusive offers.</p>
  <div class="nl-input">Enter a valid email address</div>
  <div class="nl-submit">SUBMIT</div>
</section>

<footer class="footer">
  <div class="contact-item" style="left:166px">
    <span class="contact-icon"><svg width="18" height="18" viewBox="0 0 18 18"><path d="M9 1C5.5 1 3 3.5 3 7c0 4.5 6 10 6 10s6-5.5 6-10c0-3.5-2.5-6-6-6z" fill="var(--green)"/><circle cx="9" cy="7" r="2.3" fill="#fff"/></svg></span>
    <p>ADDRESS:<br>Lorem ipsum dolor sit<br>amet, consectetur</p>
  </div>
  <div class="contact-item" style="left:504px;top:84px">
    <span class="contact-icon"><svg width="18" height="18" viewBox="0 0 18 18"><path d="M4 1l3 4-2 2c1 2.5 3 4.5 5.5 5.5l2-2 4 3-2 3C8 16 2 10 1 3z" fill="var(--green)"/></svg></span>
    <p>PHONE:<br><span style="font-size:15px">+1 555 014 2290</span></p>
  </div>
  <div class="contact-item" style="left:800px;top:84px">
    <span class="contact-icon"><svg width="18" height="18" viewBox="0 0 18 18"><rect x="2" y="4" width="14" height="10" fill="var(--green)"/><path d="M2 4l7 6 7-6" fill="none" stroke="#fff" stroke-width="1.3"/></svg></span>
    <p>EMAIL:<br>hello@brambletonpizza.com</p>
  </div>
  <div class="footer-rule"></div>
  <nav class="footer-nav">
    <a style="left:331px">Our Menus</a><i style="left:392px"></i>
    <a style="left:445px">About Us</a><i style="left:496px"></i>
    <a style="left:555px">Order Online</a><i style="left:612px"></i>
    <a style="left:654px">Gallery</a><i style="left:697px"></i>
    <a style="left:753px">Reviews</a><i style="left:803px"></i>
    <a style="left:860px">Contact Us</a>
  </nav>
</footer>

<div class="bottom-bar">
  <p class="copyright">Copyright © 2025, Company Name. All Rights Reserved.</p>
  <span class="social" style="left:999px"></span>
  <span class="social" style="left:1048px"></span>
  <span class="social" style="left:1095px"></span>
</div>

</body>
</html>
```